Cedar Brook Stables, LLC

Equestrian business card to promote equine retirement, farm sitting, short term board. Located in Aiken, SC.
Updates
Updated color schemes.
Contact Information for Business Card
Contact info, description of work.
Colors
0094D4
00A9DD
6FCCEA
C7EBF8
E9F6FB
59FF00
82FF00
B8FF75
E3FFCB
F4FFEA
F0912C
F2A743
F7CA91
FBE8D2
FDF5EE

```html
<!DOCTYPE html>
<html lang="en">
<head>
<meta charset="utf-8">
<title>Cedar Brook Stables – Business Card</title>
<link href="https://fonts.googleapis.com/css2?family=Poppins:wght@400;500;600;700&display=swap" rel="stylesheet">
<style>
  :root {
    --farm-green: #1b8416;
    --farm-green-deep: #136b10;
    --pattern-green: #2fae1f;
    --sun-yellow: #fdbb12;
    --ink: #2b2b2b;
    --rule-grey: #9a9a9a;
    --card-white: #ffffff;
    --stage: #ecebe7;
  }
  * { margin: 0; padding: 0; box-sizing: border-box; }
  html, body {
    width: 1200px; height: 900px; overflow: hidden;
    background: var(--stage);
    font-family: "Poppins", sans-serif;
  }
  .card {
    position: absolute; left: 260px;
    width: 680px; height: 389px;
    overflow: hidden;
    box-shadow: 0 6px 18px rgba(0,0,0,.18);
  }
  /* Back side */
  .card-back { top: 41px; background: var(--farm-green); }
  .back-pattern {
    position: absolute; inset: 0;
    background: radial-gradient(ellipse at 80% 10%, var(--pattern-green) 0%, var(--farm-green) 55%, var(--farm-green-deep) 100%);
  }
  .back-name {
    position: absolute; left: 0; right: 0; top: 178px;
    text-align: center; color: var(--card-white);
    font-weight: 600; font-size: 20px; letter-spacing: .5px;
  }
  /* Front side */
  .card-front { top: 470px; background: var(--card-white); }
  .front-waves { position: absolute; inset: 0; }
  .brand {
    position: absolute; left: 40px; top: 108px; width: 250px;
    display: flex; align-items: center; gap: 10px;
  }
  .brand-dot { width: 18px; height: 18px; border-radius: 50%; background: var(--farm-green); flex: none; }
  .brand-name { font-weight: 700; font-size: 21px; line-height: 1.2; color: var(--ink); }
  .divider {
    position: absolute; left: 318px; top: 34px; width: 1px; height: 160px;
    background: var(--rule-grey);
  }
  .contact { position: absolute; left: 345px; top: 28px; color: var(--ink); }
  .contact-name { font-weight: 700; font-size: 22px; color: var(--farm-green); letter-spacing: .5px; line-height: 1.1; }
  .contact-role { font-size: 14px; margin-bottom: 10px; }
  .contact-line { display: flex; align-items: center; gap: 9px; font-size: 14px; line-height: 1.5; }
  .contact-line svg { width: 16px; height: 16px; flex: none; }
  .contact-address { font-size: 14px; line-height: 1.4; margin-top: 6px; padding-left: 25px; }
  .services {
    position: absolute; left: 0; right: 0; bottom: 24px;
    display: flex; justify-content: center; align-items: center; gap: 12px;
    color: var(--card-white); font-weight: 500; font-size: 16px; letter-spacing: .5px;
  }
  .services .bullet { width: 8px; height: 8px; border-radius: 50%; background: var(--sun-yellow); }
</style>
</head>
<body>

<section class="card card-back">
  <div class="back-pattern" role="img" aria-label="Embossed repeating brand pattern in green tones"></div>
  <p class="back-name">Cedar Brook Stables, LLC</p>
</section>

<section class="card card-front">
  <svg class="front-waves" viewBox="0 0 680 389" preserveAspectRatio="none" aria-hidden="true">
    <path d="M0 262 C 170 280 360 268 500 232 C 390 280 210 306 0 298 Z" fill="var(--sun-yellow)"/>
    <path d="M0 304 C 210 306 390 274 500 244 C 575 224 630 212 680 204 L680 389 L0 389 Z" fill="var(--farm-green)"/>
  </svg>

  <div class="brand">
    <span class="brand-dot"></span>
    <span class="brand-name">Cedar Brook Stables, LLC</span>
  </div>

  <div class="divider"></div>

  <div class="contact">
    <p class="contact-name">DANIEL HAYES</p>
    <p class="contact-role">Managing Director</p>
    <p class="contact-line">
      <svg viewBox="0 0 24 24"><path fill="var(--farm-green)" d="M6.6 10.8a15 15 0 0 0 6.6 6.6l2.2-2.2c.3-.3.7-.4 1-.2 1.1.4 2.3.6 3.6.6.6 0 1 .4 1 1V20c0 .6-.4 1-1 1A17 17 0 0 1 3 4c0-.6.4-1 1-1h3.5c.6 0 1 .4 1 1 0 1.3.2 2.5.6 3.6.1.3 0 .7-.2 1z"/></svg>
      803-555 0142
    </p>
    <p class="contact-line">
      <svg viewBox="0 0 24 24"><path fill="var(--farm-green)" d="M2 5h20v14H2z"/><path d="M2 5l10 8 10-8" fill="none" stroke="#fff" stroke-width="1.6"/></svg>
      info@cedarbrookstables.com
    </p>
    <p class="contact-line">
      <svg viewBox="0 0 24 24"><circle cx="12" cy="12" r="10" fill="var(--farm-green)"/><path d="M2 12h20M12 2c3 3 3 17 0 20M12 2c-3 3-3 17 0 20" fill="none" stroke="#fff" stroke-width="1.3"/></svg>
      www.cedarbrookstables.com
    </p>
    <p class="contact-address">118 Whiskey Road,<br>Aiken, SC 29801</p>
  </div>

  <div class="services">
    <span>SHORT TERM BOARD</span><span class="bullet"></span>
    <span>FARM SITTING</span><span class="bullet"></span>
    <span>EQUINE RETIREMENT</span>
  </div>
</section>

</body>
</html>
```